VELMOR Website Design

We need a website designed for our company VELMOR. We are a luxury lifestyle club that will provide benefits and services for our members. The site should be clean & sleek, preferably using black and white (or darker colors). (example sites: stravenhall.example, plinth.example)

Here is a link of a sample page I did using wix. (https://dunmere7.sitehostly.example/mysite) This can be used to get a general idea.

Target Market(s)

Upper Middle Class in the United States

Number of Pages Required

5+ page

Font styles to use
Sans Serif
Other font styles liked:
• Arial (or other similar fonts)

Requirements
Must have
• A clean design that is eye-catching and speaks to our company.
Nice to have
• Ideas for copy.

```html
<!DOCTYPE html>
<html lang="en">
<head>
<meta charset="utf-8">
<title>VELMOR — A Members Only Lifestyle Club</title>
<link rel="stylesheet" href="https://fonts.googleapis.com/css2?family=Catamaran:wght@300;400;500;600;700&display=swap">
<style>
  :root {
    --ink: #111111;
    --text: #333333;
    --muted: #666666;
    --white: #ffffff;
    --band: #3a3a3a;
    --footer: #0d0d0d;
    --footer-text: #c9c9c9;
    --footer-dim: #6d6d6d;
    --line: #9a9a9a;
  }
  * { box-sizing: border-box; margin: 0; padding: 0; }
  html, body { width: 718px; height: 1200px; overflow: hidden; background: var(--white); }
  body { font-family: "Catamaran", Arial, sans-serif; color: var(--text); position: relative; }
  .page { position: relative; width: 718px; height: 1200px; }

  .hero {
    position: absolute; left: 0; top: 0; width: 718px; height: 259px;
    background: radial-gradient(ellipse at 55% 45%, #6b5d45 0%, #3a3326 40%, #1a1815 75%, #0f0f10 100%);
  }
  .hero-photo { position: absolute; inset: 0; }
  .brand { position: absolute; left: 71px; top: 14px; font-size: 18px; font-weight: 500; color: var(--white); letter-spacing: 0.5px; }
  .nav { position: absolute; top: 12px; right: 69px; display: flex; align-items: center; gap: 0; }
  .nav a { color: var(--white); text-decoration: none; font-size: 8px; padding: 4px 11px; }
  .nav a.is-active { border: 1px solid var(--white); border-radius: 5px; margin-right: 14px; padding: 4px 11px; }
  .nav a + a { margin-left: 2px; }
  .hero-title { position: absolute; left: 0; right: 0; top: 122px; text-align: center; color: var(--white); font-size: 26px; font-weight: 500; }

  .btn { position: absolute; left: 311px; width: 100px; height: 25px; border: 1px solid var(--line); border-radius: 5px; font-size: 8px; display: flex; align-items: center; justify-content: center; color: var(--text); text-decoration: none; }
  .btn.on-dark { color: var(--white); border-color: #cfcfcf; }

  .about-title { position: absolute; top: 294px; left: 0; right: 0; text-align: center; font-size: 13px; font-weight: 300; color: var(--text); }
  .about-title strong { font-size: 16px; font-weight: 600; color: var(--ink); }
  .about-copy { position: absolute; top: 330px; left: 120px; width: 478px; text-align: center; font-size: 8px; line-height: 17px; color: var(--text); }
  .about-copy strong { color: var(--ink); font-weight: 600; }

  .experiences { position: absolute; left: 0; top: 446px; width: 718px; height: 232px; background: linear-gradient(90deg, #4a463c 0%, #3a3a3a 14%, #3a3a3a 80%, #5a5444 92%, #6a6250 100%); }
  .experiences::after { content: ""; position: absolute; left: 0; right: 0; bottom: -22px; height: 22px; background: linear-gradient(#ececec, #ffffff); }
  .exp-title { position: absolute; top: 33px; left: 0; right: 0; text-align: center; color: var(--white); font-size: 16px; font-weight: 400; }
  .exp-item { position: absolute; top: 82px; width: 130px; color: var(--white); font-size: 7.5px; line-height: 11px; }
  .exp-item svg { display: block; margin-bottom: 17px; }

  .benefits-title { position: absolute; top: 717px; left: 0; right: 0; text-align: center; font-size: 16px; font-weight: 400; color: var(--ink); letter-spacing: 0.4px; }
  .benefits-copy { position: absolute; top: 758px; left: 98px; width: 522px; text-align: center; font-size: 7px; line-height: 14px; color: var(--muted); }

  .cards { position: absolute; top: 838px; left: 69px; display: flex; gap: 5px; }
  .card { position: relative; width: 141px; height: 139px; }
  .card-label { position: absolute; left: 14px; bottom: 14px; color: var(--white); font-size: 7.5px; font-weight: 500; letter-spacing: 0.2px; padding-left: 6px; border-left: 2px solid var(--white); line-height: 9px; }

  .footer { position: absolute; left: 0; top: 1103px; width: 718px; height: 97px; background: var(--footer); }
  .footer-links { position: absolute; right: 68px; top: 45px; display: flex; gap: 20px; }
  .footer-links a { color: var(--footer-text); text-decoration: none; font-size: 8px; }
  .copyright { position: absolute; right: 68px; top: 69px; font-size: 6.5px; color: var(--footer-dim); }
  .social { position: absolute; left: 0; top: 0; }
</style>
</head>
<body>
<div class="page">

  <header class="hero">
    <div class="hero-photo" role="img" aria-label="Photo of hands raising champagne glasses in a toast at a dim bar"></div>
    <div class="brand">VELMOR</div>
    <nav class="nav">
      <a class="is-active" href="#">Home</a>
      <a href="#">About</a>
      <a href="#">Services and Benefits</a>
    </nav>
    <h1 class="hero-title">A Members Only Lifestyle Club</h1>
  </header>

  <section>
    <h2 class="about-title">About <strong>VELMOR</strong></h2>
    <p class="about-copy"><strong>VELMOR</strong> is a members only lifestyle club founded in order to bring the best services, experiences, and opportunities to our diverse community of members. Our members consist of creatives, athletes, artists, and other professionals.</p>
    <a class="btn" style="top:382px" href="#">Learn More</a>
  </section>

  <section class="experiences" role="img" aria-label="Dark band with a softly blurred photo of wine glasses raised at the edges">
    <h2 class="exp-title">Experiences</h2>
    <div class="exp-item" style="left:127px">
      <svg width="18" height="18" viewBox="0 0 18 18" style="margin-left:45px"><rect x="1" y="3" width="14" height="14" fill="none" stroke="#fff" stroke-width="1"/><path d="M4 9 L8 13 L17 1" fill="none" stroke="#fff" stroke-width="1.2"/></svg>
      VELMOR organizes and supports a ton of private events and parties for our members.
    </div>
    <div class="exp-item" style="left:302px">
      <svg width="18" height="18" viewBox="0 0 18 18" style="margin-left:49px"><rect x="1" y="3" width="14" height="14" fill="none" stroke="#fff" stroke-width="1"/><path d="M4 9 L8 13 L17 1" fill="none" stroke="#fff" stroke-width="1.2"/></svg>
      Members are also provided access to exclusive venues and events from our partners.
    </div>
    <div class="exp-item" style="left:474px">
      <svg width="18" height="18" viewBox="0 0 18 18" style="margin-left:49px"><rect x="1" y="3" width="14" height="14" fill="none" stroke="#fff" stroke-width="1"/><path d="M4 9 L8 13 L17 1" fill="none" stroke="#fff" stroke-width="1.2"/></svg>
      Network with other members to build lasting relationships.
    </div>
    <a class="btn on-dark" style="top:180px" href="#">Learn More</a>
  </section>

  <section>
    <h2 class="benefits-title">BENEFITS AND SERVICES</h2>
    <p class="benefits-copy">VELMOR membership provides you with amazing benefits and services.Members receive access to the best accountants, attorneys, real estate agents, private bankers/advisers and more.VELMOR members also receive access to private flight travel, premium luxury gym memberships, private social clubs, and private investment opportunities.</p>
    <div class="cards">
      <div class="card" role="img" aria-label="Photo of a hand holding a pen over financial documents" style="background:linear-gradient(160deg,#3e4046,#5b5e66 60%,#2f3035)">
        <span class="card-label">ACCOUNTING SERVICES</span>
      </div>
      <div class="card" role="img" aria-label="Photo of travellers stepping off a private jet onto a red carpet" style="background:linear-gradient(180deg,#3c3b3b,#6a6663 55%,#6b2a2c)">
        <span class="card-label">PRIVATE JET TRAVEL</span>
      </div>
      <div class="card" role="img" aria-label="Photo of friends sharing food at an outdoor gathering" style="background:linear-gradient(160deg,#2e3528,#4a4a3a 55%,#3a2f2a)">
        <span class="card-label">PRIVATE EVENTS</span>
      </div>
      <div class="card" role="img" aria-label="Photo of a diver swimming beside a manta ray underwater" style="background:linear-gradient(180deg,#1f4a5a,#28566a 55%,#163846)">
        <span class="card-label">EXPERIENCES</span>
      </div>
    </div>
    <a class="btn" style="top:1014px" href="#">See All</a>
  </section>

  <footer class="footer">
    <svg class="social" width="300" height="97" viewBox="0 0 300 97" aria-label="Social links">
      <circle cx="87" cy="49" r="16" fill="none" stroke="#555" stroke-width="1"/>
      <circle cx="138" cy="49" r="16" fill="none" stroke="#555" stroke-width="1"/>
      <circle cx="189" cy="49" r="16" fill="none" stroke="#555" stroke-width="1"/>
      <circle cx="239" cy="49" r="16" fill="none" stroke="#555" stroke-width="1"/>
    </svg>
    <nav class="footer-links">
      <a href="#">About</a>
      <a href="#">Services and Benefits</a>
      <a href="#">Contact Us</a>
    </nav>
    <p class="copyright">© 2018 by Northlight Studio.</p>
  </footer>

</div>
</body>
</html>
```